Design a label for a dog shampoo names fluffo, the sell point of this series of shampoo is “just like wash your dogs with milk, not harm for your hand ”, the style could be gentle or professional or even amazing.

Use only 2 colors in the design job, the color of our logo could be changed, it depends on your whole page. Please design in CDR or ai.

update:
Pls do more change with the fonts when you design the front page, including title and details. Try more styles of fonts. Addition, this design will be printed on the bottle, no a label stick on it.
Updates

Do not put a real dog or animal on the page, Pay more attention to the types of fonts

Reason: Expect for more design idea.

Target Market(s)

people 20-30 years old who have dogs and cats at home

Industry/Entity Type

It Professional

Requirements
Nice to have
• It would be nice if you add some detail words in the design of the right side.

```html
<!DOCTYPE html>
<html lang="en">
<head>
<meta charset="utf-8">
<title>FLUFFO Shampoo Label</title>
<link href="https://fonts.googleapis.com/css2?family=Arimo:wght@400;700&display=swap" rel="stylesheet">
<style>
  :root {
    --ink: #1b5e9f;
    --brand: #4a8ec0;
    --paper: #ffffff;
  }
  * { margin: 0; padding: 0; box-sizing: border-box; }
  html, body { width: 1200px; height: 2297px; overflow: hidden; background: var(--paper); }
  .label {
    position: relative;
    width: 1200px;
    height: 2297px;
    background: var(--paper);
    color: var(--ink);
    font-family: "Arimo", Arial, sans-serif;
    text-align: center;
  }
  .brand-name {
    position: absolute;
    top: 300px;
    left: 0;
    width: 1200px;
    font-size: 120px;
    line-height: 134px;
    font-weight: 400;
    letter-spacing: 26px;
    color: var(--brand);
  }
  .intro {
    position: absolute;
    top: 557px;
    left: 90px;
    width: 1020px;
    font-size: 36.5px;
    line-height: 50px;
  }
  .section {
    position: absolute;
    left: 80px;
    width: 1040px;
    font-size: 31.5px;
    line-height: 41.6px;
  }
  .section h2 {
    font-size: 31.5px;
    font-weight: 700;
    line-height: 41.6px;
  }
  .section p { font-weight: 400; }
  .directions { top: 1114px; }
  .precautions { top: 1504px; }
  .storage { top: 1769px; }
  .ingredients { top: 1908px; }
</style>
</head>
<body>
  <main class="label">
    <h1 class="brand-name">FLUFFO</h1>

    <p class="intro">
      FLUFFO Super-Conditioning &amp; Nutrient Shampoo is<br>
      a specially formulated shampoo, rich in conditioners<br>
      picked up from milk which subdivide and balance<br>
      nutrition of pet’s coat. More easier and better<br>
      assimilate for coat from base to the end after using.<br>
      With the help of minus-ion, the balancer of nutrition,<br>
      rinses out quickly and completely to leave a soft,<br>
      sparkling, and smooth coat. Safe and gentle enough<br>
      to be used every day. Safe for the most sensitive<br>
      skin and coat, puppies, lactating bitches and cats.
    </p>

    <section class="section directions">
      <h2>Directions:</h2>
      <p>
        1. Before shampooing, blush out pet’s coat.<br>
        2. Saturate dog’s coat with lukewarm water.<br>
        3. Dispense a small amount of shampoo into the your hand.<br>
        4. To clean coat, start at dog’s head and work back towards the<br>
        tail. Avoid getting shampoo into the dog’s eyes and ears.<br>
        5. Rinse coat sereral times with lukewarm water.<br>
        6. Towel dry and gently comb or brush coat.
      </p>
    </section>

    <section class="section precautions">
      <h2>Use Precautions:</h2>
      <p>
        Harmful if swallowed. Do not inhale. Discontinue use if<br>
        irritation develops and contact your veterinarian. For animal<br>
        use only. Not for human use. Keep out of reach of children.<br>
        Do not decant into smaller containers. Not for injection.<br>
        Always consult with a Veterinarian for systemic conditions.
      </p>
    </section>

    <section class="section storage">
      <h2>Storage and Disposal:</h2>
      <p>
        Keep out of the tough of children. Replace Cap. Wrap in<br>
        several layers of newspaper and discard in trash.
      </p>
    </section>

    <section class="section ingredients">
      <h2>Active Ingredients:</h2>
      <p>Hypochlorous Acid, Sodium Hypochlorite</p>
    </section>
  </main>
</body>
</html>
```